Business Card design for law firm = Brightvale Australia

We are seeking a new design for our business cards.
We are keeping our logo, which is attached.
We need space for
Name
Title
Address is , which is
Level 7
214 Marlowe Street
Sydney NSW 2047
Phone :
Mobile :
Fax :
Email :
DX :
website www.brightvale-example.com.au

Industry/Entity Type

Law Firm / Banking and Finance

Contact Information for Business Card

We are seeking a new design for our business cards. We are keeping our logo. We need space for Name Title Address is Level 7 214 Marlowe Street Sydney NSW 2047 Phone Mobile Fax Email DX website www.brightvale-example.com.au

Colors
0054AA
0677BA
7BADD7
CADEEF
E8F1F8

Requirements
Must have
• see our website for general feel www.brightvale-example.com.au

```html
<!DOCTYPE html>
<html lang="en">
<head>
<meta charset="utf-8">
<title>Brightvale Australia – Business Card</title>
<link rel="stylesheet" href="https://fonts.googleapis.com/css2?family=Crimson+Pro:wght@400&display=swap">
<style>
  :root {
    --page-bg: #2e2e2f;
    --card-top: #1d1e20;
    --card-bottom: #2b2c2e;
    --brand-blue: #3152a6;
    --brand-cyan: #1a9bc7;
    --text-light: #e4e4e4;
    --text-muted: #5a5c60;
    --mark-dark: #151617;
  }
  * { margin: 0; padding: 0; box-sizing: border-box; }
  html, body {
    width: 1200px; height: 1138px; overflow: hidden;
    background: var(--page-bg);
    font-family: "Crimson Pro", Georgia, serif;
  }
  .card {
    position: absolute;
    left: 273px; width: 620px; height: 376px;
    border-radius: 16px;
    overflow: hidden;
    background: linear-gradient(160deg, var(--card-top), var(--card-bottom));
  }
  .card--front { top: 184px; }
  .card--back { top: 606px; }

  .front-name {
    position: absolute; left: 0; right: 0; top: 155px;
    text-align: center;
    font-size: 52px; line-height: 1;
    color: var(--mark-dark);
  }

  .brand-name {
    position: absolute; left: 34px; top: 44px;
    font-size: 46px; line-height: 1;
    color: var(--brand-blue);
  }

  .person { position: absolute; left: 34px; top: 208px; }
  .person__name { font-size: 25px; color: var(--brand-blue); line-height: 1.1; }
  .person__title { font-size: 16px; color: var(--text-light); line-height: 1.2; }

  .contacts {
    position: absolute; left: 34px; top: 294px;
    display: flex; gap: 18px;
    font-size: 14.5px; line-height: 23px;
  }
  .contact-col { display: flex; flex-direction: column; }
  .contact-row { display: flex; align-items: center; gap: 9px; white-space: nowrap; }
  .contact-row svg { width: 13px; height: 13px; flex: none; fill: var(--brand-cyan); }
  .contact-col--phone { color: var(--text-muted); }
  .contact-col--web, .contact-col--address { color: var(--text-light); }
  .address-lines { display: flex; gap: 8px; }
  .address-lines svg { width: 12px; height: 15px; margin-top: 4px; fill: var(--brand-cyan); flex: none; }

  .card__band {
    position: absolute; left: 0; right: 0; bottom: 0; height: 5px;
    background: var(--brand-blue);
  }
</style>
</head>
<body>

<section class="card card--front" aria-label="Card front">
  <p class="front-name">Brightvale</p>
</section>

<section class="card card--back" aria-label="Card back">
  <p class="brand-name">Brightvale</p>

  <div class="person">
    <p class="person__name">Sam Whitlock</p>
    <p class="person__title">Managing Director</p>
  </div>

  <div class="contacts">
    <div class="contact-col contact-col--phone">
      <div class="contact-row">
        <svg viewBox="0 0 16 16" aria-hidden="true"><path d="M2 5c0-2 2-3 6-3s6 1 6 3v1h-3V5H5v1H2zM4 7h8l2 6H2zM8 8.5a2 2 0 1 0 0 4 2 2 0 0 0 0-4z"/></svg>
        <span>02 9000 4182</span>
      </div>
      <div class="contact-row">
        <svg viewBox="0 0 16 16" aria-hidden="true"><path d="M4 1h8v4H4zM1 6h14v6h-3v3H4v-3H1zM5 10v4h6v-4z"/></svg>
        <span>02 9000 4190</span>
      </div>
    </div>

    <div class="contact-col contact-col--web">
      <div class="contact-row">
        <svg viewBox="0 0 16 16" aria-hidden="true"><path d="M1 3h14v10H1zM2.5 4.5 8 9l5.5-4.5v7h-11z" fill-rule="evenodd"/></svg>
        <span>sam.whitlock@brightvale-example.com.au</span>
      </div>
      <div class="contact-row">
        <svg viewBox="0 0 16 16" aria-hidden="true"><path d="M8 1a7 7 0 1 0 0 14A7 7 0 0 0 8 1zm0 1.5c.8.8 1.5 2.3 1.7 4H6.3C6.5 4.8 7.2 3.3 8 2.5zM2.6 7.5h2.2c.1-1.6.5-3 1.2-4a5.5 5.5 0 0 0-3.4 4zm0 1a5.5 5.5 0 0 0 3.4 4c-.7-1-1.1-2.4-1.2-4zm3.7 0h3.4c-.2 1.700-.9 3.2-1.7 4-.8-.8-1.5-2.3-1.7-4zm4.9 0h2.2a5.5 5.5 0 0 1-3.4 4c.7-1 1.1-2.4 1.2-4zm2.2-1h-2.2c-.1-1.6-.5-3-1.2-4a5.5 5.5 0 0 1 3.4 4z"/></svg>
        <span>https://www.brightvale-example.com.au</span>
      </div>
    </div>

    <div class="contact-col contact-col--address">
      <div class="address-lines">
        <svg viewBox="0 0 12 16" aria-hidden="true"><path d="M6 0a6 6 0 0 0-6 6c0 4.5 6 10 6 10s6-5.5 6-10a6 6 0 0 0-6-6zm0 3.5a2.5 2.5 0 1 1 0 5 2.5 2.5 0 0 1 0-5z"/></svg>
        <div>
          <p>Level 7 214 Marlowe St</p>
          <p>Sydney NSW 2047</p>
        </div>
      </div>
    </div>
  </div>

  <div class="card__band"></div>
</section>

</body>
</html>
```